Velvet Lantern rebranding my business with a new business card

I have my new logo and now I need a refresher on my business cards. I really want something fun and fresh. I like black background or anything to make the color pop.
Logo
Name: Velvet Lantern
Contact Info as stated below:
Mira Pellow
555-013-4762
Logo
Name: Velvet Lantern
Mira Pellow
555-013-4762
fb.me/VelvetLanternbyMira
Instagram: @VelvetLanternbyMira

Industry/Entity Type

Business

Contact Information for Business Card

double-sided. Logo on one side. Contact info on the other.

Requirements
Must have
• Logo
• Name: Velvet Lantern
• Contact Info as stated below:
• Mira Pellow
• 555-013-4762
• fb.me/VelvetLanternbyMira
• fb.me/VelvetLanternbyMira

```html
<!DOCTYPE html>
<html lang="en">
<head>
<meta charset="utf-8">
<title>Velvet Lantern – Business Card</title>
<link rel="stylesheet" href="https://fonts.googleapis.com/css2?family=Ubuntu:wght@400;500&family=Patrick+Hand&display=swap">
<style>
  :root {
    --stage: #dcdcdc;
    --card: #fbfbfb;
    --ink: #1f1f1f;
    --teal: #6cc7b5;
    --pink: #f6c9cf;
    --pink-soft: #fbe0e3;
    --ring: #1f1f1f;
  }
  * { margin: 0; padding: 0; box-sizing: border-box; }
  html, body { width: 1200px; height: 576px; overflow: hidden; }
  body {
    background: var(--stage);
    font-family: "Ubuntu", sans-serif;
    color: var(--ink);
    position: relative;
  }
  .card {
    position: absolute;
    top: 138px;
    width: 484px;
    height: 294px;
    background: var(--card);
    border-radius: 14px;
    overflow: hidden;
    box-shadow: 0 2px 5px rgba(0,0,0,0.18);
  }
  .card--front { left: 82px; }
  .card--back { left: 602px; }

  /* Front */
  .front-emblem {
    position: absolute;
    left: 138px;
    top: 42px;
    width: 208px;
    height: 208px;
    border: 2px solid var(--ring);
    border-radius: 50%;
    display: flex;
    align-items: center;
    justify-content: center;
    text-align: center;
  }
  .brand-name {
    font-family: "Ubuntu", sans-serif;
    font-weight: 500;
    color: var(--teal);
    line-height: 1.1;
  }
  .front-emblem .brand-name { font-size: 30px; }
  .front-strip {
    position: absolute;
    left: 0; right: 0; bottom: 0;
    height: 7px;
    display: flex;
  }
  .front-strip__teal { flex: 0 0 355px; background: var(--teal); }
  .front-strip__pink { flex: 1; background: var(--pink); }

  /* Back */
  .back-wave { position: absolute; left: 0; top: 0; }
  .back-brand {
    position: absolute;
    left: 36px;
    top: 78px;
    width: 190px;
    text-align: center;
  }
  .back-brand .brand-name { font-size: 30px; }
  .holder {
    position: absolute;
    right: 26px;
    top: 40px;
    text-align: right;
  }
  .holder__name {
    font-family: "Patrick Hand", cursive;
    font-size: 33px;
    letter-spacing: 1px;
    line-height: 1;
  }
  .holder__role {
    font-size: 12px;
    margin-top: 6px;
  }
  .contacts {
    position: absolute;
    right: 26px;
    top: 216px;
    list-style: none;
    text-align: right;
  }
  .contact {
    display: flex;
    align-items: center;
    justify-content: flex-end;
    gap: 6px;
    font-size: 17px;
    height: 26px;
  }
  .contact__icon {
    width: 18px;
    height: 18px;
    border: 1.5px solid var(--ink);
    border-radius: 4px;
    display: inline-flex;
    align-items: center;
    justify-content: center;
  }
</style>
</head>
<body>
  <section class="card card--front" aria-label="Card front">
    <div class="front-emblem">
      <span class="brand-name">Velvet<br>Lantern</span>
    </div>
    <div class="front-strip">
      <span class="front-strip__teal"></span>
      <span class="front-strip__pink"></span>
    </div>
  </section>

  <section class="card card--back" aria-label="Card back">
    <svg class="back-wave" width="484" height="294" viewBox="0 0 484 294" aria-hidden="true">
      <path d="M0,236 C110,290 300,240 484,152 L484,294 L0,294 Z" fill="var(--teal)"/>
      <path d="M0,212 C150,252 320,210 484,138" fill="none" stroke="var(--pink)" stroke-width="9"/>
      <path d="M0,226 C140,262 320,226 484,152" fill="none" stroke="var(--pink-soft)" stroke-width="6"/>
    </svg>

    <div class="back-brand">
      <span class="brand-name">Velvet Lantern</span>
    </div>

    <div class="holder">
      <p class="holder__name">Mira Pellow</p>
      <p class="holder__role">Managing Director</p>
    </div>

    <ul class="contacts">
      <li class="contact">
        <span>555-013-4762</span>
        <span class="contact__icon">
          <svg width="11" height="11" viewBox="0 0 24 24" aria-hidden="true">
            <path d="M6.6 10.8a15 15 0 0 0 6.6 6.6l2.2-2.2a1 1 0 0 1 1-.25 11.4 11.4 0 0 0 3.6.57 1 1 0 0 1 1 1V20a1 1 0 0 1-1 1A17 17 0 0 1 3 4a1 1 0 0 1 1-1h3.5a1 1 0 0 1 1 1c0 1.25.2 2.45.57 3.6a1 1 0 0 1-.25 1z" fill="var(--ink)"/>
          </svg>
        </span>
      </li>
      <li class="contact">
        <span>VelvetLanternbyMira</span>
        <span class="contact__icon"></span>
      </li>
    </ul>
  </section>
</body>
</html>
```